Single-sided business card for restaurant velmora with new logo made on this site

Business card options with new logo including restaurant name, address, phone number and website. This business card is single-sided only and will be presented at the hostess desk for clients to take. I would like to see options based on a cream card background, a white card background, a yellow card background and a burgundy colored background. It needs to be elegant and traditional.

Target Market(s)

local and international crowd

Industry/Entity Type

restaurant

Contact Information for Business Card

address, website and phone number

Font styles to use
Serif

Colors
EE7325
F08F49
F5BC92
FAE3D3
FDF4ED

Requirements
Must have
• new logo, address, phone number, website
Should not have
• more than three colors

```html
<!DOCTYPE html>
<html lang="es">
<head>
<meta charset="utf-8">
<title>Velmora – Tarjeta de presentación</title>
<link rel="stylesheet" href="https://fonts.googleapis.com/css2?family=Crimson+Text:wght@400;600&display=swap">
<style>
  :root {
    --backdrop: #2e2e2e;
    --frame: #3b1c1a;
    --card: #ffffff;
    --card-shade: #ececec;
    --gold: #e8a630;
    --ink: #3b1c1a;
    --text: #555555;
    --leaf: #e4e4e4;
  }
  * { margin: 0; padding: 0; box-sizing: border-box; }
  html, body {
    width: 1200px; height: 900px; overflow: hidden;
    background: var(--backdrop);
  }
  .canvas {
    width: 1200px; height: 900px;
    display: flex; align-items: center; justify-content: center;
  }
  .business-card {
    width: 1000px; height: 572px;
    background: var(--frame);
    padding: 26px;
    box-shadow: 0 20px 40px rgba(0,0,0,.45);
  }
  .card-face {
    position: relative;
    width: 100%; height: 100%;
    background: linear-gradient(100deg, var(--card) 0%, var(--card) 45%, var(--card-shade) 70%, var(--card) 100%);
    overflow: hidden;
    font-family: "Crimson Text", Georgia, serif;
  }
  .backdrop-motif {
    position: absolute; right: 0; top: 0;
    width: 460px; height: 420px;
    background: radial-gradient(ellipse at 70% 40%, var(--leaf) 0%, rgba(228,228,228,.5) 45%, rgba(255,255,255,0) 75%);
  }
  .brand {
    position: absolute; left: 90px; top: 200px;
    display: flex; align-items: center; gap: 22px;
  }
  .brand-square {
    width: 64px; height: 64px; background: var(--gold);
  }
  .brand-name {
    font-size: 66px; font-weight: 600; color: var(--ink);
    letter-spacing: 10px; line-height: 1;
  }
  .contact-list {
    position: absolute; left: 520px; top: 300px;
    list-style: none;
    font-size: 27px; color: var(--text); line-height: 1.2;
  }
  .contact-item {
    display: flex; align-items: flex-start; gap: 16px;
    margin-bottom: 14px;
  }
  .contact-icon { width: 24px; height: 24px; flex: none; margin-top: 6px; }
  .contact-icon path, .contact-icon circle { fill: var(--gold); }
</style>
</head>
<body>
<main class="canvas">
  <article class="business-card">
    <div class="card-face">
      <div class="backdrop-motif" role="img" aria-label="Faint decorative motif in light grey"></div>

      <div class="brand">
        <span class="brand-square"></span>
        <h1 class="brand-name">VELMORA</h1>
      </div>

      <ul class="contact-list">
        <li class="contact-item">
          <svg class="contact-icon" viewBox="0 0 24 24" aria-hidden="true">
            <path d="M3 9c0-3 4-5 9-5s9 2 9 5v2h-5V9H8v2H3z M5 13h14l1 7H4z"/>
          </svg>
          <span>958-214-3307</span>
        </li>
        <li class="contact-item">
          <svg class="contact-icon" viewBox="0 0 24 24" aria-hidden="true">
            <circle cx="12" cy="12" r="10"/>
          </svg>
          <span>www.velmora.com.mx</span>
        </li>
        <li class="contact-item">
          <svg class="contact-icon" viewBox="0 0 24 24" aria-hidden="true">
            <path d="M12 1a7 7 0 0 0-7 7c0 5 7 15 7 15s7-10 7-15a7 7 0 0 0-7-7zm0 10a3 3 0 1 1 0-6 3 3 0 0 1 0 6z"/>
          </svg>
          <span>Orquídea 415<br>Bahías de Santa Cruz, Oaxaca CP 70980</span>
        </li>
      </ul>
    </div>
  </article>
</main>
</body>
</html>
```